Lindqvar Foundation Letterhead

We are a newly established non profit registered in Maryland but operates in Africa, south of the sahara. We offer scholarships to deserving young adults from high school through college. Our color theme for our existing logo is purple, we want a design that is stylish, spellbinding yet a letterhead that projects seriousness. More information on www.thelindqvarfoundation.example

Target Market(s)

High school and college students in sub saharan African as well as our donors in the US

Industry/Entity Type

Non Profit

Font styles to use
Script

Requirements
Must have
• Logo at the top and if possible watermark the logo in the middle of the letterhead, contact address,
Should not have
• NA

```html
<!DOCTYPE html>
<html lang="en">
<head>
<meta charset="utf-8">
<title>Lindqvar Foundation Letterhead</title>
<link href="https://fonts.googleapis.com/css2?family=Cabin:wght@400;500&display=swap" rel="stylesheet">
<style>
  :root {
    --backdrop: #e4e4e6;
    --paper: #ffffff;
    --purple: #5b2a8e;
    --purple-light: #8a5cbf;
    --ink: #2e2e33;
    --muted: #6a6a70;
  }
  * { box-sizing: border-box; margin: 0; padding: 0; }
  html, body { width: 1200px; height: 795px; overflow: hidden; }
  body {
    background: var(--backdrop);
    font-family: "Cabin", "Gill Sans", sans-serif;
    color: var(--ink);
    display: flex; align-items: center; justify-content: center;
  }
  .letterhead {
    position: relative;
    width: 532px; height: 752px;
    background: var(--paper);
    box-shadow: 0 6px 22px rgba(0,0,0,.14);
    overflow: hidden;
  }
  .brand {
    position: absolute; top: 40px; left: 0; right: 0;
    display: flex; flex-direction: column; align-items: center; gap: 8px;
  }
  .brand-mark {
    width: 34px; height: 34px; border-radius: 50%;
    background: var(--purple);
  }
  .brand-name {
    font-size: 17px; letter-spacing: .08em; text-transform: uppercase;
    color: var(--purple); font-weight: 400;
  }
  .brand-tagline {
    font-size: 6.5px; letter-spacing: .16em; text-transform: uppercase;
    color: var(--purple-light); margin-top: -5px;
  }
  .letter {
    position: absolute; top: 188px; left: 48px; right: 48px;
    font-size: 8.6px; line-height: 1.45; color: var(--ink);
  }
  .letter p { margin-bottom: 9px; }
  .salutation { margin-bottom: 11px !important; }
  .sign-off {
    position: absolute; left: 48px; top: 520px;
    font-size: 8.6px; line-height: 1.5; color: var(--muted);
  }
  .signature {
    display: block; width: 90px; height: 22px; margin: 4px 0 6px;
    background: linear-gradient(90deg, rgba(30,30,30,.55), rgba(30,30,30,.15));
    border-radius: 11px;
  }
  .contact {
    position: absolute; right: 40px; top: 602px; text-align: right;
    font-size: 8.6px; line-height: 1.5; color: var(--ink);
  }
  .contact-name {
    color: var(--purple); font-size: 10.5px; letter-spacing: .08em; text-transform: uppercase;
  }
  .contact-label { color: var(--purple-light); }
  .footer-lines {
    position: absolute; left: 0; right: 0; bottom: 46px; height: 6px;
    border-top: 1px solid var(--purple);
    border-bottom: 2px solid var(--purple-light);
  }
  .footer-band {
    position: absolute; left: 0; right: 0; bottom: 0; height: 40px;
    background: var(--purple);
    display: flex; align-items: center; justify-content: flex-end; padding-right: 40px;
    color: #fff; font-size: 10px; letter-spacing: .32em;
  }
</style>
</head>
<body>
  <main class="letterhead">
    <header class="brand">
      <span class="brand-mark"></span>
      <span class="brand-name">Lindqvar Foundation Inc</span>
      <span class="brand-tagline">Scholarships for a brighter tomorrow</span>
    </header>

    <section class="letter">
      <p class="salutation">Dear Mr. John,</p>
      <p>Lorem Ipsum is simply dummy text of the printing and typesetting industry. Lorem Ipsum has been the industry's standard dummy text ever since the 1500s, when an unknown printer took a galley of type and scrambled it to make a type specimen book. It has survived not only five centuries, but also the leap into electronic typesetting, remaining essentially unchanged.</p>
      <p>The standard chunk of Lorem Ipsum used since the 1500s is reproduced below for those interested. Sections 1.10.32 and 1.10.33 from "de Finibus Bonorum et Malorum" by Cicero are also reproduced in their exact original form, accompanied by English versions from the 1914 translation by H. Rackham.</p>
      <p>Lorem Ipsum is simply dummy text of the printing and typesetting industry. Lorem Ipsum has been the industry's standard dummy text ever since the 1500s, when an unknown printer took a galley of type and scrambled it to make a type specimen book. It has survived not only five centuries, but also the leap into electronic typesetting, remaining essentially unchanged. It was popularised in the</p>
    </section>

    <div class="sign-off">
      Sincerely Your,
      <span class="signature" role="img" aria-label="Handwritten signature"></span>
      Name Last Name<br>Company Name
    </div>

    <address class="contact" style="font-style:normal">
      <div class="contact-name">The Lindqvar Foundation Inc</div>
      <div>12 Willow Crest Lane, Suite 3, Ellicott City, Md 21043</div>
      <div><span class="contact-label">Email:</span> admin@thelindqvarfoundation.example</div>
    </address>

    <div class="footer-lines"></div>
    <footer class="footer-band">www.thelindqvarfoundation.example</footer>
  </main>
</body>
</html>
```